Elegant, High End Integrated Wellness Healthcare Practice

We need a brochure designed for an integrated mind-body wellness healthcare practice (www.quellarivecare.com) . This brochure will be used when we cold call prospects (physicians to refer to our office, and potential consumers to utilize our services). Our practice is geographically located in the middle Tennessee USA region, although we have plans to become an international company as many of our offerings can be accessed anywhere in the world. Ultimately our goal is to have this brochure used as a leave-behind in an effort to introduce our integrated offerings to increase market share. The final product brochure should be both elegant and serious, with clean lines but also convey warmth and trust, as individuals who are coming for our services have usually struggled with their health for a significant amount of time before finding our practice.
Updates

The design brief was very specific about providing a high-end science-based 2-page brochure (not flier). Several designs submitted were fliers. The other designs were heavy on yoga or "woo woo" non-science-based looking pictures. This is a flier to appeal to physicians and other healthcare providers. Therefore the design must speak science and evidence-based methods of mind and body wellness care. I would also like to appeal to the other designers I paid extra for their submissions and who have indicated they will "respond in the coming days."

```html
<!DOCTYPE html>
<html lang="en">
<head>
<meta charset="utf-8">
<title>Quellarive Care – Wellness Flyer</title>
<link rel="stylesheet" href="https://fonts.googleapis.com/css2?family=Poppins:wght@400;500;600;700&display=swap">
<style>
:root{
  --green:#6ea544;
  --green-light:#8cc063;
  --green-dark:#243a1e;
  --navy:#1c2b52;
  --navy-deep:#0e1530;
  --gray-box:#c9cec5;
  --gray-soft:#dfe3dc;
  --text:#2a2a2a;
  --page:#eceeea;
}
*{margin:0;padding:0;box-sizing:border-box}
html,body{width:1200px;height:2824px;overflow:hidden;background:var(--page);font-family:'Poppins',sans-serif;color:var(--text)}
.flyer{position:absolute;left:30px;top:603px;width:980px;height:1390px;transform:scale(1.16327);transform-origin:0 0;background:#fff;box-shadow:0 6px 24px rgba(0,0,0,.18);overflow:hidden}
.abs{position:absolute}
.header{left:0;top:0;width:980px;height:190px;background:linear-gradient(180deg,#ffffff 0%,#f3f4f2 60%,#d9dcd6 100%)}
.brand{left:300px;top:38px;display:flex;align-items:center;gap:22px}
.brand-mark{width:100px;height:100px;border-radius:50%;background:var(--green)}
.brand-name{font-weight:500;font-size:40px;line-height:56px;color:var(--green-dark);letter-spacing:1px}
.hero{left:0;top:190px;width:980px;height:373px;background:var(--navy-deep)}
.hero-photo{left:380px;top:0;width:600px;height:373px;background:linear-gradient(100deg,#141d3c 0%,#1f3466 45%,#7a8aa6 70%,#c9b48a 85%,#7b5a3a 100%)}
.hero-box{left:35px;top:55px;width:345px;height:233px;background:var(--green);padding:6px}
.hero-box-inner{width:100%;height:100%;border:1.5px solid var(--green-light);padding:14px 14px}
.hero-title{color:#fff;font-weight:700;font-size:29px;line-height:36px}
.hero-lines{color:#fff;font-weight:600;font-size:19px;line-height:30px;margin-top:14px}
.services-area{left:0;top:563px;width:605px;height:742px;background:linear-gradient(180deg,#f4f6f1 0%,#ffffff 30%,#ffffff 60%,#eef1ea 100%)}
.section-title{left:0;top:580px;width:605px;text-align:center;font-weight:700;font-size:38px;color:#1a1a1a;letter-spacing:.5px}
.section-title span{color:var(--green)}
.tile{top:644px;width:148px;height:147px;display:flex;align-items:center;justify-content:center;text-align:center;color:#fff;font-weight:600;font-size:15.5px;line-height:20px;text-shadow:0 1px 3px rgba(0,0,0,.6)}
.tile-body{left:0;background:linear-gradient(180deg,#a8bd6a,#5f7e3c)}
.tile-brain{left:152px;background:linear-gradient(180deg,#2f4a3e,#1b2c24)}
.tile-pack{left:304px;background:linear-gradient(180deg,#c9cf9e,#8a9a5c)}
.tile-nutri{left:456px;background:linear-gradient(180deg,#3e5a3b,#233528)}
.intro{left:25px;top:818px;width:556px;font-size:14.6px;line-height:17.6px;text-align:justify}
.tagline{left:25px;top:997px;font-weight:600;font-size:17px;color:var(--green)}
.card{top:1052px;height:246px;padding:30px 14px 0;text-align:center;font-size:14.5px;line-height:19.5px}
.card h3{font-weight:600;font-size:14.8px;line-height:19.5px;margin-bottom:12px}
.card-wellness{left:0;width:198px;background:var(--gray-box)}
.card-brain{left:202px;width:198px;background:var(--navy);color:#fff}
.card-brain h3{color:var(--green-light)}
.card-call{left:405px;width:200px;background:var(--gray-soft)}
.card-call h3{margin-bottom:30px}
.info{left:605px;top:563px;width:337px;height:597px;background:var(--green)}
.info-inner{position:absolute;left:12px;top:72px;width:313px;height:510px;border:1.5px solid var(--green-light)}
.info-text{position:absolute;left:12px;top:72px;width:313px;padding:10px 10px 0;color:#fff;font-size:14.3px;line-height:17.6px}
.info-text h2{font-weight:700;font-size:21px;line-height:24px}
.info-text .sub{font-size:18px;line-height:24px;margin-bottom:18px;max-width:260px}
.info-text p{margin-bottom:17px}
.info-photo{left:605px;top:1160px;width:337px;height:138px;background:linear-gradient(180deg,#cfd9e2 0%,#9fb2c6 55%,#56708c 100%)}
.side-fill{left:942px;top:563px;width:38px;height:742px;background:linear-gradient(180deg,#f4f6f1,#e9ece5)}
.rule{left:0;top:1305px;width:980px;height:5px;background:var(--green)}
.footer{left:0;top:1313px;width:980px;height:77px;background:var(--green-dark);color:#fff}
.addr{left:50px;top:19px;font-size:16px;line-height:20px}
.phone{left:400px;top:27px;font-weight:600;font-size:22px;color:var(--green-light)}
.contact{left:660px;top:14px;font-size:16.5px;line-height:22px}
.contact span{display:inline-block;width:32px}
</style>
</head>
<body>
<main class="flyer">
  <header class="abs header">
    <div class="abs brand">
      <div class="brand-mark"></div>
      <div class="brand-name">Quellarive<br>Care</div>
    </div>
  </header>

  <section class="abs hero">
    <div class="abs hero-photo" role="img" aria-label="Hand touching a tablet with a glowing digital brain beside natural remedies, herbs and fruit"></div>
    <div class="abs hero-box">
      <div class="hero-box-inner">
        <div class="hero-title">Find A Clearer Path<br>To A Healthier You</div>
        <div class="hero-lines">Our Healthy Lifestyle for Life<br>60 Day Package Offers<br>Reduced Brain Fog</div>
      </div>
    </div>
  </section>

  <section class="abs services-area"></section>
  <div class="abs side-fill"></div>
  <h2 class="abs section-title">FEATURED <span>SERVICES</span></h2>

  <div class="abs tile tile-body" role="img" aria-label="Person in a stretching pose in a sunny field">WHOLE BODY<br>WELLNESS</div>
  <div class="abs tile tile-brain" role="img" aria-label="Hands holding a glowing brain">BRAIN WAVE<br>MAPPING</div>
  <div class="abs tile tile-pack" role="img" aria-label="Open hands with soft light">WELLNESS<br>PACKAGE</div>
  <div class="abs tile tile-nutri" role="img" aria-label="Prescription pad with stethoscope and vegetables">NUTRITIONAL<br>WELLNESS</div>

  <p class="abs intro">The practitioners at Quellarive Care have significant experience working with whole-body approaches to care. Whole body health requires that the body and mind are aligned. Although pharmaceuticals and “talk therapy” can be beneficial we have found that these methods often fall short to address concerns that brought the individual to our office. Body changes are often missing. When one’s body changes the mind can more readily integrate other parts of a person’s approach to life. The result is integrative healing-oriented care that addresses aspects of the whole person (body, mind, and spirit).</p>
  <p class="abs tagline">Find a clearer path to a healthier you</p>

  <div class="abs card card-wellness">
    <h3>WELLNESS PACKAGE</h3>
    We offer a unique wellness package you won’t find anywhere else, a combination of a body and mind system designed to <b>“Reunite”</b> your brain and your gut!
  </div>
  <div class="abs card card-brain">
    <h3>PERSONALIZED BRAIN WAVE SYNCHRONIZATION PRESENTATION</h3>
    Help for Depression, Anxiety, ADHD, and Fibromyalgia and Diabetes.“Reunite” your brain and your gut!
  </div>
  <div class="abs card card-call">
    <h3>REQUEST A<br>CONSULTATION<br>CALL</h3>
    Inquiries for our healthy lifestyle for life package.
  </div>

  <aside class="abs info">
    <div class="info-inner"></div>
    <div class="info-text">
      <h2>Quellarive Care,</h2>
      <div class="sub">Integrated Body and Mind Health, Wellness Center Located in Cedarvale, TN</div>
      <p>At Quellarive Care we facilitate body and mind health and wellness through an integrated functional approach to care.</p>
      <p>This method of personalized care appreciates you as a unique individual with distinct health circumstances. We tailor our body and mind approaches to address your specific health concerns. Through the combination of body and mind interventions, we address concerns such as Attention Deficit, Distractibility and learning concerns, chronic pain and inflammation conditions, and mind health conditions such as anxiety, depression, panic, and many more.</p>
    </div>
  </aside>
  <div class="abs info-photo" role="img" aria-label="Two people raising joined hands on a mountain top above misty blue ridges"></div>

  <div class="abs rule"></div>
  <footer class="abs footer">
    <div class="abs addr">418 Linden Hollow Road,<br>Cedarvale, TN, United States, 37199</div>
    <div class="abs phone">+1 615-555-0142</div>
    <div class="abs contact"><span>E:</span>hello@quellarivecare.com<br><span>W:</span>www.quellarivecare.com</div>
  </footer>
</main>
</body>
</html>
```